Clinic for cellulit and fat removal

Name of clinic :
Lirava
- Body & Health (this has to be written on the site.)
I need CMS for me to be able to make changes myself.
A webpage for woman searching for a solution to remove fat and cellulit.
The owner is a brazilian woman in Denmark, and want her sense of aestetic shines thru the website.
There needs to be a slide show on the landing page showing big sliding pictures, of the clinic and and the treatments.
The Cryolipolysis, is a treatment freezing fat and cellulit, and this treatment will be the Attraction of the clinic.
Needs These pages in a horisontal fasion. (written in Danish)
Lirava
Behandlinger
- Cryolipolysis
- Trimflox
- Lymfemassage
- Korathelix
- Amberline Tide
Produkter
Priser
Kontakt
Clinic
Coded - Design and coding required
5+ page

```html
<!DOCTYPE html>
<html lang="da">
<head>
<meta charset="utf-8">
<title>Lirava – Body &amp; Health</title>
<link href="https://fonts.googleapis.com/css2?family=Raleway:ital,wght@0,400;0,500;0,600;0,700;0,800;1,400&display=swap" rel="stylesheet">
<style>
:root{
  --teal:#22b2d3;
  --teal-dark:#1a9fc0;
  --orange:#f7a21b;
  --orange-dark:#f08b12;
  --ink:#222;
  --text:#555;
  --muted:#999;
  --light:#f4f4f4;
  --dark:#333;
  --darker:#262626;
  --white:#fff;
}
*{box-sizing:border-box;margin:0;padding:0}
html,body{width:1200px;height:2899px;overflow:hidden}
body{font-family:"Raleway",sans-serif;color:var(--text);background:var(--white);position:relative}
.wrap{width:1050px;margin:0 auto;position:relative}
.btn{display:inline-block;background:linear-gradient(var(--orange),var(--orange-dark));color:var(--white);font-weight:600;font-size:14px;text-transform:uppercase;text-align:center;border-radius:2px;letter-spacing:.3px}

/* top bar */
.topbar{height:46px;background:var(--light);font-size:14px;color:#666}
.topbar .wrap{display:flex;justify-content:space-between;align-items:center;height:46px}
.socials{display:flex;gap:14px}
.socials span{width:14px;height:14px;border-radius:50%;background:#999;display:block}
.contact-mini{display:flex;gap:28px;align-items:center}
.contact-mini span{display:flex;align-items:center;gap:7px}

/* nav */
.nav{height:58px;background:var(--white)}
.nav .wrap{display:flex;justify-content:space-between;align-items:center;height:58px}
.brand{font-size:26px;font-weight:700;color:var(--ink);letter-spacing:.5px}
.menu{display:flex;align-items:center;gap:38px;font-size:14px;font-weight:700;color:var(--ink)}
.menu .active{color:var(--teal)}
.menu .btn{padding:11px 23px;font-size:13px}

/* hero */
.hero{height:559px;position:relative;background:linear-gradient(110deg,#8a6fa8 0%,#b9b7c8 30%,#d8d8dc 55%,#c9c3c0 80%,#a7a2a6 100%)}
.hero h1{position:absolute;top:240px;width:100%;text-align:center;color:var(--white);font-size:66px;font-weight:800;letter-spacing:1px}
.dots{position:absolute;top:516px;left:0;right:0;display:flex;justify-content:center;gap:8px}
.dots i{width:13px;height:13px;border-radius:50%;background:var(--white);display:block}
.dots i:first-child{background:var(--teal)}

/* welcome */
.welcome{height:326px;text-align:center;padding-top:43px}
.sec-title{color:var(--teal);font-size:28px;font-weight:700;text-transform:uppercase}
.welcome p{width:1050px;margin:24px auto 0;font-size:15px;line-height:27px;color:var(--text)}
.welcome .btn{margin-top:29px;width:180px;line-height:44px}

/* treatments */
.treatments{height:244px;background:var(--light);text-align:center;padding-top:40px}
.treatments .lead{font-size:15px;margin-top:23px}
.tabs{display:flex;gap:19px;position:absolute;top:1134px;left:75px}
.tab{width:195px;height:99px;background:var(--white);font-size:15px;font-weight:700;color:#444;display:flex;align-items:center;justify-content:center;text-transform:uppercase}
.tab.active{background:var(--teal);color:var(--white);border-top:6px solid var(--darker)}
.panel{height:394px;background:var(--teal)}
.panel .wrap{display:flex;gap:30px;padding-top:50px}
.panel-photo{width:422px;height:295px;border:5px solid #7fd2e6;background:linear-gradient(120deg,#e9eef2,#cfd6dc 60%,#b9c1c8)}
.panel h2{color:var(--white);font-size:26px;font-weight:700;margin-top:15px}
.panel p{color:var(--white);font-size:15px;line-height:27px;margin-top:14px;width:590px}
.panel .btn{margin-top:23px;width:226px;line-height:43px}

/* news & testimonials */
.feed{height:487px}
.feed .wrap{display:flex;padding-top:45px}
.col{width:525px;position:relative}
.col.news{border-right:1px solid #e4e4e4;height:420px}
.col.quotes{padding-left:30px}
.col h2{color:var(--teal);font-size:28px;font-weight:700;text-transform:uppercase}
.news-item{display:flex;gap:18px;margin-top:28px}
.news-item:first-of-type{margin-top:30px}
.date{width:72px;height:72px;border-radius:50%;overflow:hidden;flex:none;border:2px solid #ddd;text-align:center}
.date .m{background:var(--darker);color:var(--white);font-size:12px;font-weight:700;height:28px;line-height:30px}
.date .d{background:var(--orange);color:var(--white);font-size:28px;font-weight:800;height:42px;line-height:38px}
.news-item h3{color:var(--teal);font-size:15px;font-weight:600;text-transform:uppercase}
.news-item p{font-size:15px;line-height:26px;margin-top:5px;width:420px}
.news-item a{color:var(--orange);font-size:11px;font-weight:700;text-transform:uppercase;display:block;margin-top:6px}
.col .btn{position:absolute;top:356px;width:180px;line-height:44px}
.arrows{position:absolute;right:0;top:8px;display:flex;gap:16px}
.quote-mark{color:var(--teal);font-size:52px;font-weight:800;line-height:30px;margin-top:22px;height:30px}
.quotes blockquote{font-style:italic;font-size:15px;line-height:27px;margin-top:14px;width:495px}
.person{display:flex;align-items:center;gap:22px;margin-top:18px}
.avatar{width:100px;height:100px;border-radius:50%;background:linear-gradient(#c59b7a,#7a5a46);border:3px solid #e6e6e6}
.person h4{color:var(--teal);font-size:13px;font-weight:700;text-transform:uppercase}
.person small{font-style:italic;font-size:13px;color:var(--muted)}

/* banner */
.banner{height:324px;position:relative;background:linear-gradient(90deg,#3b3b3b,#55504c 45%,#4a4758 75%,#3a3a3a)}
.banner h2{position:absolute;top:120px;width:100%;text-align:center;color:var(--white);font-size:37px;font-weight:800}
.banner .btn{position:absolute;top:181px;left:487px;width:226px;line-height:44px}

/* contact boxes */
.contacts{height:170px}
.contacts .wrap{display:flex;justify-content:space-between;padding-top:29px}
.cbox{width:330px;height:99px;background:linear-gradient(#45c3e0,var(--teal-dark));display:flex;align-items:center;gap:20px;padding-left:36px;color:var(--white);font-weight:700;font-size:20px}
.cbox.addr{font-size:17px;line-height:24px}
.ring{width:52px;height:52px;border-radius:50%;border:2px solid var(--white);display:flex;align-items:center;justify-content:center;flex:none}

/* footer */
.footer{height:232px;background:var(--dark);color:#ddd}
.footer .wrap{display:flex;padding-top:42px}
.fcol h4{color:var(--white);font-size:14px;font-weight:600;text-transform:uppercase;margin-bottom:10px}
.fcol li{list-style:none;font-size:13px;line-height:27px}
.fcol.sitemap{width:229px}
.fcol.treat{width:250px}
.fcol.newsletter{width:336px}
.field{width:242px;height:38px;background:var(--white);color:#888;font-size:12px;padding:12px 10px;margin-bottom:10px}
.newsletter .btn{margin-left:152px;width:90px;line-height:36px;font-size:13px}
.fsocial{display:flex;gap:16px;margin-top:14px}
.fsocial span{width:18px;height:18px;border-radius:50%;background:#aaa;display:block}
.copyright{height:59px;background:var(--darker);color:#ccc;font-size:13px;text-align:center;line-height:59px}
</style>
</head>
<body>

<header>
  <div class="topbar">
    <div class="wrap">
      <div class="socials" aria-label="Sociale medier"><span></span><span></span><span></span><span></span><span></span></div>
      <div class="contact-mini">
        <span><svg width="12" height="12" viewBox="0 0 24 24"><path fill="#22b2d3" d="M6.6 10.8a15 15 0 0 0 6.6 6.6l2.2-2.2a1 1 0 0 1 1-.3 11.4 11.4 0 0 0 3.6.6 1 1 0 0 1 1 1V20a1 1 0 0 1-1 1A17 17 0 0 1 3 4a1 1 0 0 1 1-1h3.5a1 1 0 0 1 1 1 11.4 11.4 0 0 0 .6 3.6 1 1 0 0 1-.3 1z"/></svg>1-800-555-0147</span>
        <span><svg width="13" height="11" viewBox="0 0 24 18"><path fill="#22b2d3" d="M0 0h24v18H0z"/><path fill="none" stroke="#f4f4f4" stroke-width="2" d="M1 1l11 9 11-9"/></svg>info@lirava.com</span>
        <span><svg width="12" height="12" viewBox="0 0 24 24"><circle cx="12" cy="12" r="11" fill="#22b2d3"/><path fill="none" stroke="#f4f4f4" stroke-width="1.5" d="M1 12h22M12 1c-4 4-4 18 0 22M12 1c4 4 4 18 0 22"/></svg>English ⌄</span>
      </div>
    </div>
  </div>
  <nav class="nav">
    <div class="wrap">
      <div class="brand">LIRAVA</div>
      <div class="menu">
        <span class="active">LIRAVA</span><span>BEHANDLINGER</span><span>PRODUKTER</span><span>PRISER</span><span>KONTAKT</span>
        <span class="btn">Book an appointment</span>
      </div>
    </div>
  </nav>
</header>

<section class="hero" role="img" aria-label="Slideshow photo: therapist in blue gloves performing a cryolipolysis treatment on a woman lying in the clinic">
  <h1>BODY &amp; HEALTH</h1>
  <div class="dots"><i></i><i></i><i></i><i></i></div>
</section>

<section class="welcome">
  <h2 class="sec-title">Welcome to Lirava</h2>
  <p>Aliquam molestie, mi et imperdiet euismod, dui purus auctor tellus, et interdum lacus lectus et ante. Sed accumsan sollicitudin sapien, sit amet adipiscing turpis gravida ac. In congue, neque ac lobortis volutpat, libero mauris varius mi, vitae suscipit ipsum ligula vitae risus. Duis aliquam nibh a dui iaculis viverra id a velit. Vivamus egestas risus in magna varius commodo. Sed semper viverra egestas. Etiam pretium porttitor lectus, vel ornare neque porta volutpat.</p>
  <span class="btn">Read more</span>
</section>

<section class="treatments">
  <h2 class="sec-title">Behandlinger</h2>
  <p class="lead">Aliquam molestie, mi et imperdiet euismod, dui purus auctor tellus, et interdum lacus lectus et ante.</p>
</section>
<div class="tabs">
  <div class="tab active">Cryolipolysis</div>
  <div class="tab">Trimflox</div>
  <div class="tab">Lymfemassage</div>
  <div class="tab">Korathelix</div>
  <div class="tab">Amberline Tide</div>
</div>
<section class="panel">
  <div class="wrap">
    <div class="panel-photo" role="img" aria-label="Photo of a woman relaxing on a treatment bed beside a cryolipolysis machine"></div>
    <div>
      <h2>THE CRYOLIPOLYSIS</h2>
      <p>Aliquam molestie, mi et imperdiet euismod, dui purus auctor tellus, et interdum lacus lectus et ante. Sed accumsan sollicitudin sapien, sit amet adipiscing turpis gravida ac. In congue, neque ac lobortis volutpat, libero mauris varius mi, vitae suscipit ipsum ligula vitae risus. Duis aliquam nibh a dui iaculis viverra id a velit. Vivamus egestas risus in magna varius commodo. Sed semper viverra egestas. Etiam pretium porttitor lectus.</p>
      <span class="btn">Book an appointment</span>
    </div>
  </div>
</section>

<section class="feed">
  <div class="wrap">
    <div class="col news">
      <h2>Latest News</h2>
      <div class="news-item">
        <div class="date"><div class="m">APR</div><div class="d">10</div></div>
        <div><h3>Aliquam molestie, mi et imperdiet euismod</h3><p>Dui purus auctor tellus, et interdum lacus lectus et ante a nibh eget turpis vehicula tempus ac sed massa..</p><a>Read more</a></div>
      </div>
      <div class="news-item">
        <div class="date"><div class="m">APR</div><div class="d">10</div></div>
        <div><h3>Aliquam molestie, mi et imperdiet euismod</h3><p>Dui purus auctor tellus, et interdum lacus lectus et ante a nibh eget turpis vehicula tempus ac sed massa..</p><a>Read more</a></div>
      </div>
      <span class="btn">Read all news</span>
    </div>
    <div class="col quotes">
      <h2>Testimonials</h2>
      <div class="arrows">
        <svg width="14" height="22" viewBox="0 0 14 22"><path d="M12 2L3 11l9 9" fill="none" stroke="#333" stroke-width="3"/></svg>
        <svg width="14" height="22" viewBox="0 0 14 22"><path d="M2 2l9 9-9 9" fill="none" stroke="#333" stroke-width="3"/></svg>
      </div>
      <div class="quote-mark">“</div>
      <blockquote>Dui purus auctor tellus, et interdum lacus lectus et ante a nibh eget turpis vehicula tempus ac sed massa habitant morbi tristique senectus et netus et malesuada fames ac turpis egestas. Nunc consequat congue nulla eu imperdiet dignissim lectus vitae..”</blockquote>
      <div class="person">
        <div class="avatar" role="img" aria-label="Portrait photo of the client giving the testimonial"></div>
        <div><h4>Name Heading</h4><small>Location</small></div>
      </div>
      <span class="btn" style="left:30px">Read all</span>
    </div>
  </div>
</section>

<section class="banner" role="img" aria-label="Photo of a woman in shorts holding a small chalkboard in front of her hips">
  <h2>CELLULIT AND FAT REMOVAL CLINIC</h2>
  <span class="btn">Book an appointment</span>
</section>

<section class="contacts">
  <div class="wrap">
    <div class="cbox"><span class="ring"><svg width="24" height="24" viewBox="0 0 24 24"><path fill="#fff" d="M6.6 10.8a15 15 0 0 0 6.6 6.6l2.2-2.2a1 1 0 0 1 1-.3 11.4 11.4 0 0 0 3.6.6 1 1 0 0 1 1 1V20a1 1 0 0 1-1 1A17 17 0 0 1 3 4a1 1 0 0 1 1-1h3.5a1 1 0 0 1 1 1 11.4 11.4 0 0 0 .6 3.6 1 1 0 0 1-.3 1z"/></svg></span>1-800-555-0147</div>
    <div class="cbox"><span class="ring"><svg width="24" height="18" viewBox="0 0 24 18"><rect width="24" height="18" rx="2" fill="#fff"/><path fill="none" stroke="#22b2d3" stroke-width="2" d="M1 1l11 9 11-9"/></svg></span>info@lirava.com</div>
    <div class="cbox addr"><span class="ring"><svg width="20" height="26" viewBox="0 0 20 26"><path fill="none" stroke="#fff" stroke-width="2.2" d="M10 25S2 15 2 9.5a8 8 0 0 1 16 0C18 15 10 25 10 25z"/><circle cx="10" cy="9.5" r="3" fill="#fff"/></svg></span><span>4127 Fernmoor Road,<br>Glasgow</span></div>
  </div>
</section>

<footer>
  <div class="footer">
    <div class="wrap">
      <div class="fcol sitemap"><h4>Site Map</h4><ul><li>Lirava</li><li>Behandlinger</li><li>Produkter</li><li>Priser</li><li>Kontakt</li></ul></div>
      <div class="fcol treat"><h4>Behandlinger</h4><ul><li>Cryolipolysis</li><li>Trimflox</li><li>Lymfemassage</li><li>Korathelix</li><li>Amberline Tide</li></ul></div>
      <div class="fcol newsletter"><h4>Newsletter Sign Up</h4><div class="field">Enter Name</div><div class="field">Enter Email Address</div><span class="btn">Sign up</span></div>
      <div class="fcol"><h4>Connect Us</h4><div class="fsocial"><span></span><span></span><span></span><span></span><span></span></div></div>
    </div>
  </div>
  <div class="copyright">Copyright © 2017. Company Name.All Right Reserved</div>
</footer>

</body>
</html>
```